Professional Single Page Website Design for Tollbrook Advisory

Tollbrook Advisory is a new business consultancy specializing in providing expert services to small businesses, primarily in the brick-and-mortar retail and food service sectors. We offer a range of services including franchise development and launch, due diligence, and construction management.

Currently, we have a basic website set up at www.tollbrookadvisory.example, but we need a professional touch to enhance its design and functionality.

Project Requirements:
- Single Page Design: For now, we need a single page design that effectively showcases who we are, our services, and contact information.
- Future Expansion: The design should be flexible and scalable for future expansion to include additional pages like specific service offerings, about us, and a dedicated contact page.
- Design Aesthetic: We are looking for a modern yet professional design that aligns with our brand identity.
- Logo: We have a logo that we like, which was also sourced from Pixel Bazaar. The logo files are attached to this project brief.

Key Sections to Include:
- Hero Section: An engaging introduction to Tollbrook Advisory with a strong visual impact.
- About Us: A brief overview of who we are and our mission.
- Team: Section for the profiles of the two principals.
- Services: A clear and concise presentation of our services, including franchise development, due diligence, and construction management.
- Contact Information: Easy-to-find contact details, including a form for inquiries.
- Call to Action: Encouraging visitors to get in touch with us for consultations or further information.

Design Considerations:
- Ensure the design is responsive and mobile-friendly.
- Include high-quality images and icons that complement our services and industry.
- We do not need development services, this is only a design project.

```html
<!DOCTYPE html>
<html lang="en">
<head>
<meta charset="utf-8">
<title>Tollbrook Advisory — Business Consultancy</title>
<link href="https://fonts.googleapis.com/css2?family=Poppins:wght@400;500;600;700&display=swap" rel="stylesheet">
<style>
:root{
  --green:#8ec9ab;
  --green-deep:#3f9b6f;
  --green-soft:#a9d7bf;
  --ink:#1d1f22;
  --text:#4a4f55;
  --muted:#8a9096;
  --white:#ffffff;
  --grey-bg:#efefef;
  --black:#0a0a0a;
}
*{box-sizing:border-box;margin:0;padding:0}
html,body{width:1200px;height:3696px;overflow:hidden}
body{font-family:"Poppins",sans-serif;color:var(--text);background:var(--white);position:relative}
.brand{display:flex;align-items:center;gap:12px;font-weight:600;font-size:20px;color:var(--green-deep);white-space:nowrap}
.brand-mark{width:30px;height:30px;background:var(--green-deep);flex:none}
.btn{display:inline-block;font-family:"Poppins",sans-serif;font-weight:500;border:none;border-radius:4px;font-size:15px;padding:12px 26px;white-space:nowrap}
.btn-green{background:var(--green);color:var(--ink)}
.btn-dark{background:var(--ink);color:var(--white)}
.btn-white{background:var(--white);color:var(--ink)}

/* nav */
.site-nav{position:absolute;top:0;left:0;width:1200px;height:88px;display:flex;align-items:center;padding:0 100px 0 112px;background:var(--white)}
.site-nav ul{display:flex;gap:34px;list-style:none;margin-left:auto;margin-right:70px;font-size:15px;color:var(--ink);white-space:nowrap}
.site-nav .btn{padding:10px 22px}

/* hero */
.hero{position:absolute;top:88px;left:0;width:1200px;height:640px;overflow:hidden}
.hero-photo{position:absolute;inset:0;background:linear-gradient(100deg,#2b2622 0%,#4b3d33 35%,#8a7665 65%,#6e6a68 100%)}
.hero-shade{position:absolute;inset:0;background:linear-gradient(90deg,rgba(0,0,0,.55),rgba(0,0,0,.1) 60%)}
.hero-copy{position:absolute;left:112px;top:145px;width:560px;color:var(--white)}
.hero-copy h1{font-size:52px;line-height:1.12;font-weight:700}
.hero-copy .tagline{font-size:21px;margin-top:22px}
.hero-copy p{font-size:15px;line-height:1.6;margin-top:20px;width:500px}
.hero-copy .btn{margin-top:28px}
.hero-curve{position:absolute;left:0;bottom:0}

/* about */
.about{position:absolute;top:760px;left:0;width:1200px;height:560px}
.about-visual{position:absolute;left:96px;top:20px}
.about-copy{position:absolute;left:600px;top:20px;width:500px}
.about-copy h2{font-size:40px;font-weight:600;color:var(--ink)}
.about-copy h3{font-size:22px;font-weight:600;color:var(--green-deep);margin-top:8px}
.about-copy p{font-size:14px;line-height:1.75;margin-top:10px}
.about-copy h3.mission{margin-top:22px}
.about-copy .btn{margin-top:22px}

/* services */
.services{position:absolute;top:1380px;left:0;width:1200px;height:380px;background:var(--green);text-align:center}
.services h2{font-size:40px;font-weight:600;color:var(--white);margin-top:24px}
.service-tabs{display:flex;justify-content:center;gap:22px;margin-top:40px}
.service-tab{background:var(--white);color:var(--ink);font-size:14px;font-weight:500;line-height:1.25;padding:10px 16px;border-radius:4px;width:200px}
.service-tab.active{background:var(--ink);color:var(--white)}
.services p{width:1110px;margin:52px auto 0;font-size:15px;line-height:1.8;color:var(--white)}

.team-photo{position:absolute;top:1760px;left:0;width:1200px;height:540px;
  background:
    linear-gradient(180deg,rgba(255,255,255,0) 55%,rgba(60,70,80,.35) 100%),
    linear-gradient(110deg,#3c4650 0%,#6d8496 22%,#b7c6d2 45%,#e6ebef 62%,#aebbc6 80%,#56626c 100%)}

/* leadership */
.leadership{position:absolute;top:2300px;left:0;width:1200px;height:500px;background:var(--grey-bg)}
.leadership-intro{position:absolute;left:140px;top:150px}
.leadership-intro h2{font-size:38px;font-weight:600;line-height:1.3;color:var(--ink)}
.leadership-intro .btn{margin-top:26px;padding:12px 22px}
.leader-card{position:absolute;top:52px;width:248px;height:400px;background:var(--white)}
.leader-card .portrait{height:160px;background:linear-gradient(180deg,#b9c4cc,#7d8b95)}
.leader-card .info{padding:18px 20px}
.leader-card h3{font-size:22px;font-weight:600;color:var(--ink)}
.leader-card .role{font-size:14px;color:var(--text)}
.leader-card p{font-size:11px;line-height:1.6;color:var(--muted);margin-top:10px}
.leader-card .contact-icons{display:flex;gap:18px;margin-top:16px}

/* contact */
.contact{position:absolute;top:2800px;left:0;width:1200px;height:440px}
.contact-form{position:absolute;left:0;top:0;width:480px;height:440px;background:var(--green-soft);padding:26px 34px}
.contact-form h2{font-size:34px;font-weight:600;color:var(--ink)}
.form-grid{display:grid;grid-template-columns:1fr 1fr;gap:18px 40px;margin-top:24px;width:400px}
.field{background:var(--white);height:36px;border-radius:3px;font-size:11px;color:var(--muted);padding:4px 10px}
.field.wide{grid-column:1/3;height:74px}
.contact-form .btn{margin-top:28px;font-size:14px}
.map{position:absolute;left:480px;top:0;width:720px;height:440px;background:linear-gradient(135deg,#dcdcdc,#c9c9c9 50%,#e2e2e2)}
.map-pin{position:absolute;left:320px;top:170px}
.address-box{position:absolute;left:225px;top:248px;width:270px;padding:10px;background:var(--green);color:var(--ink);font-size:13px;line-height:1.5;text-align:center;white-space:nowrap}

/* footer */
.site-footer{position:absolute;top:3240px;left:0;width:1200px;height:456px;background:var(--black);color:var(--white)}
.site-footer .brand{position:absolute;left:112px;top:90px;color:var(--white)}
.site-footer .brand-mark{background:var(--green)}
.footer-about{position:absolute;left:112px;top:196px;width:330px;font-size:14px;line-height:1.6}
.footer-social{position:absolute;left:520px;top:170px}
.footer-social h3,.newsletter h3{font-size:26px;font-weight:600}
.social-row{display:flex;gap:10px;margin-top:22px}
.social-row span{width:22px;height:22px;border:1px solid var(--white);border-radius:50%}
.newsletter{position:absolute;left:840px;top:170px;width:250px}
.newsletter .field{margin-top:22px;background:transparent;border:1px solid var(--white);color:#bbb;height:34px;padding:8px 10px}
.newsletter .btn{display:block;width:250px;text-align:center;margin-top:20px;color:var(--ink);padding:8px}
.footer-bottom{position:absolute;left:112px;right:100px;top:405px;display:flex;font-size:14px}
.footer-bottom nav{margin-left:auto;display:flex;gap:40px}
</style>
</head>
<body>

<header class="site-nav">
  <div class="brand"><span class="brand-mark"></span>Tollbrook Advisory</div>
  <ul>
    <li>Home</li><li>About Us</li><li>Our Services</li><li>Our Team</li><li>Contact Us</li>
  </ul>
  <span class="btn btn-green">Get In Touch</span>
</header>

<section class="hero">
  <div class="hero-photo" role="img" aria-label="Two business consultants reviewing plans on a tablet in a brick office"></div>
  <div class="hero-shade"></div>
  <div class="hero-copy">
    <h1>Building Success in Southern California</h1>
    <div class="tagline">Expertise at Every Step: From Planning to Execution</div>
    <p>At Tollbrook, we blend innovative strategies with local market expertise to guide your commercial real estate venture.</p>
    <span class="btn btn-white">Learn More</span>
  </div>
  <svg class="hero-curve" width="1200" height="120" viewBox="0 0 1200 120">
    <path d="M0 60 Q600 150 1200 40 L1200 120 L0 120 Z" fill="#ffffff"/>
    <path d="M0 56 Q600 146 1200 36" fill="none" stroke="#8ec9ab" stroke-width="6"/>
  </svg>
</section>

<section class="about">
  <svg class="about-visual" width="380" height="500" viewBox="0 0 380 500" role="img" aria-label="Construction workers in safety vests on a building site, framed in three house-shaped windows">
    <defs>
      <linearGradient id="site" x1="0" y1="0" x2="0" y2="1">
        <stop offset="0" stop-color="#b9d2e4"/><stop offset="0.6" stop-color="#8aa0b0"/><stop offset="1" stop-color="#5d6b63"/>
      </linearGradient>
    </defs>
    <path d="M10 120 L120 40 L120 480 L10 480 Z" fill="url(#site)"/>
    <path d="M135 30 L190 0 L245 30 L245 480 L135 480 Z" fill="url(#site)"/>
    <path d="M260 40 L370 120 L370 480 L260 480 Z" fill="url(#site)"/>
    <path d="M0 120 L120 34 M260 34 L380 120" stroke="#3f9b6f" stroke-width="6" fill="none"/>
  </svg>
  <div class="about-copy">
    <h2>About us</h2>
    <h3>Who We Are</h3>
    <p>Welcome to Tollbrook Advisory, your trusted partner in navigating the complexities of the real estate and small business markets. Founded by industry veterans Owen Hartley and Daniel Reyes, we specialize in providing comprehensive services tailored to the unique needs of our clients. Whether you're a franchisee or a new restaurant owner.</p>
    <h3 class="mission">Our Mission</h3>
    <p>Lorem ipsum dolor sit amet, consectetur adipiscing elit, sed do eiusmod tempor incididunt ut labore et dolore magna aliqua. Ut enim ad minim veniam, quis nostrud exercitation ullamco laboris nisi ut aliquip ex ea commodo consequat.</p>
    <span class="btn btn-dark">Learn More</span>
  </div>
</section>

<section class="services">
  <h2>Our Services</h2>
  <div class="service-tabs">
    <div class="service-tab">Franchise Development &amp; Launch</div>
    <div class="service-tab">Due Diligence Services</div>
    <div class="service-tab active">Building &amp; Construction Management</div>
    <div class="service-tab">Investment Property Evaluation</div>
    <div class="service-tab">Market Analysis &amp; Feasibility Studies</div>
  </div>
  <p>Our Building &amp; Construction Management Services oversee every aspect of your construction and development projects, from initial planning to final completion. We ensure projects stay on time and within budget, providing meticulous attention to detail and proactive problem-solving. Specializing in tenant improvements (TIs) and ground-up construction for small to mid-size commercial projects, we handle everything from permitting and contractor coordination to quality control and final inspections. Trust us to deliver successful projects that meet your specifications and exceed your expectations, ensuring a smooth and efficient construction process every step of the way.</p>
</section>

<div class="team-photo" role="img" aria-label="Team of consultants gathered around a table reviewing documents in a bright office"></div>

<section class="leadership">
  <div class="leadership-intro">
    <h2>Our Leadership<br>Team</h2>
    <span class="btn btn-green">Read Bio details</span>
  </div>
  <article class="leader-card" style="left:532px">
    <div class="portrait" role="img" aria-label="Portrait of principal Daniel Reyes"></div>
    <div class="info">
      <h3>Daniel Reyes</h3>
      <div class="role">Principal</div>
      <p>Daniel Reyes is a seasoned real estate expert with extensive experience in project and new construction management across the region.</p>
      <div class="contact-icons">
        <svg width="18" height="14" viewBox="0 0 18 14"><rect x="1" y="1" width="16" height="12" fill="none" stroke="#1d1f22" stroke-width="1.6"/><path d="M1 1 L9 8 L17 1" fill="none" stroke="#1d1f22" stroke-width="1.6"/></svg>
        <svg width="16" height="16" viewBox="0 0 24 24"><path d="M6.6 10.8a15 15 0 0 0 6.6 6.6l2.2-2.2c.3-.3.7-.4 1-.2 1.1.4 2.3.6 3.6.6.6 0 1 .4 1 1V20c0 .6-.4 1-1 1A17 17 0 0 1 3 4c0-.6.4-1 1-1h3.5c.6 0 1 .4 1 1 0 1.3.2 2.5.6 3.6.1.3 0 .7-.2 1z" fill="#1d1f22"/></svg>
      </div>
    </div>
  </article>
  <article class="leader-card" style="left:820px">
    <div class="portrait" role="img" aria-label="Portrait of principal Owen Hartley"></div>
    <div class="info">
      <h3>Owen Hartley</h3>
      <div class="role">Principal</div>
      <p>Owen Hartley brings over 20 years of experience as a real estate broker and a proven record in retail and food service development.</p>
      <div class="contact-icons">
        <svg width="18" height="14" viewBox="0 0 18 14"><rect x="1" y="1" width="16" height="12" fill="none" stroke="#1d1f22" stroke-width="1.6"/><path d="M1 1 L9 8 L17 1" fill="none" stroke="#1d1f22" stroke-width="1.6"/></svg>
        <svg width="16" height="16" viewBox="0 0 24 24"><path d="M6.6 10.8a15 15 0 0 0 6.6 6.6l2.2-2.2c.3-.3.7-.4 1-.2 1.1.4 2.3.6 3.6.6.6 0 1 .4 1 1V20c0 .6-.4 1-1 1A17 17 0 0 1 3 4c0-.6.4-1 1-1h3.5c.6 0 1 .4 1 1 0 1.3.2 2.5.6 3.6.1.3 0 .7-.2 1z" fill="#1d1f22"/></svg>
      </div>
    </div>
  </article>
</section>

<section class="contact">
  <div class="contact-form">
    <h2>Contact Us</h2>
    <div class="form-grid">
      <div class="field">First Name</div>
      <div class="field">Last Name</div>
      <div class="field">Phone</div>
      <div class="field">E-mail</div>
      <div class="field">Company</div>
      <div class="field">Location</div>
      <div class="field wide">Additional Information</div>
    </div>
    <span class="btn btn-dark">Send Message</span>
  </div>
  <div class="map" role="img" aria-label="Street map of the office area">
    <svg class="map-pin" width="50" height="66" viewBox="0 0 50 66"><path d="M25 2C12 2 2 12 2 25c0 17 23 39 23 39s23-22 23-39C48 12 38 2 25 2z" fill="#8ec9ab"/><circle cx="25" cy="24" r="8" fill="#ffffff"/></svg>
    <div class="address-box">410 Harbor Dr Suite 200<br>410 Harbor Dr, Costa Verde, CA 92700</div>
  </div>
</section>

<footer class="site-footer">
  <div class="brand"><span class="brand-mark"></span>Tollbrook Advisory</div>
  <p class="footer-about">Lorem ipsum dolor sit amet, consectetur adipiscing elit, sed do eiusmod tempor incididunt ut labore et dolore magna aliqua.</p>
  <div class="footer-social">
    <h3>Follow us</h3>
    <div class="social-row"><span></span><span></span><span></span><span></span><span></span></div>
  </div>
  <div class="newsletter">
    <h3>Newsletter</h3>
    <div class="field">Enter Your E-mail</div>
    <span class="btn btn-green">Subscribe</span>
  </div>
  <div class="footer-bottom">
    <span>©2024 Tollbrook Advisory. All rights reserved.</span>
    <nav><span>Privacy Policy</span><span>Terms and conditions</span></nav>
  </div>
</footer>

</body>
</html>
```